Digital Imaging Website Design Project

This project is for 3 page designs - The main Home page design, department page design & content page design which will utilize most of the home page components.

Client Background - http://www.qvzprint.example

An almost Forty year old established printing company that has a large client base of architect/engineering, as the print shop opened up as a blueprinting company, and over the years has grown, changed and expanded to offer document and digital file management for this industry. KLMVxco. has also always offered color printing services, but recently has expanded their color department to be able to offer amazing dimensional printing, and extreme cutting technology.

These new products and services will be targeted to new industries for repeatable printing needs, promotional, point of purchase color printing, as well as in-store, interior decor/wall. These new printing services are only offered by KLMVXCO in their area, and they want to convey that they are on the leading edge of color printing technology, while at the same time, not eliminating their existing primary business scaring away their traditional client base of architectural/engineering firms that use them for large format printing, scanning and document management services.

1 - Home Page Design
Primary Goals of the design:

1.Provide a new, eye catching engaging website that conveys the above expansion/growth/cutting edge company.
2.Full screen design please to move away from the 'center' bordered up website they currently have.
3.Design Components – We don't have any media to provide you with exception of our logo. We're looking for fresh design that is exciting and engaging imagery. Additionally, we are working on a color/effected version of our logo to place on the color division page, and this will probably tie in with the design you create for us.
4.It should be designed to be able to work as a responsive design as well so that when installed, will work across devices etc..
5.Colors – Same color scheme, but if you have an accent color you'd like to use to make the site pop, go for it!

Requirements:
1.The 4 divisions of the company should be the main feature so that the client depending on which department they are needing, will see those 4 choices clearly in the design, and they'll know to click on one of them to get more information and to their needed services.

2.The main goal of the site is to get visitors to place an order, there should be a feature on the home page for this call to action.

3.Put in an element that communicates the main benefit of KLMVxco. - an area for a 1-line Statement/Call to Action / Overall Company Benefit/

4.The 4 divisions need to have eye catching elements related to their products and services, and that clearly illustrate that the user should click on that to go to the appropriate area for products and services

Reprographics
This department is specifically geared to architect/engineering industry
BYLine for optional Use: Partnering with Building Industry Providers since 1975
Related pages for better understanding:
http://www.klmvxco.example/services/portland_professional_printing_services
http://www.klmvxco.example/services/reprographics
Digital File Management
This department is related to Architect/engineers, but can also apply to any other industry needing electronic document management, scanning, or archival services.
BYLine for optional use: Effective & Efficient Digital Solutions at every level.
Related Pages:
http://www.klmvxco.example/colorgraphics/electronic_file_document_management
http://www.klmvxco.example/colorgraphics/document_scanning_service
http://www.klmvxco.example/services/scanning_and_archiving

Color Graphics
This Department is newly expanded / has expanded services / they are focusing more of their efforts on this department and is a key reason for updated website design.
This Department image/representation should be stellar in the imagery to convey the excellence of the color department the services availble.
One of their newest products/services is dimensional printing – not 3-D, but raised element printing. Essentially a client could pick components on their graphic that that they want to 'bump' out, and additional layers would be put in place to create a popped out, dimensional effect. * Bonus points for creating the color department image that effectively conveys this new service – whether it's showing an abstract image/element that is actually raised off the page/paper/component. Additionally the color dimensional printing can be done on practically any material – glass, vinyl, material etc.... Please let me know if you have any questions on this.
BYLine for optional Use: See How Our Color Stands Out From the Rest
Related pages:
http://www.klmvxco.example/colorgraphics
http://www.klmvxco.example/colorgraphics/color_digital_imaging

Equipment & Supplies
This department provides specific supplies and hardware vs. printing products/services. Our largest client base is architects/engineers, but is not limited to this industry. Typical equipment is large printers, and supplies are typically paper products geared to the large format printing services, for the architect/engineers industry.
Byline for optional Use: In-House Printing & Fulfillment Services
Related pages:
http://www.klmvxco.example/tarvo_ulix_equipment_sales
http://www.klmvxco.example/supplies

Additionally - Possibly have descriptive text sections below these 4 elements, but this is optional.

2.) Department/Division Page design -

This page should pull the home page element to over based on which division is selected.
Have a submenu design incorporated so that users can navigate to all the products and services that will be listed under that division
Contain a plugin design for FAQs – so that depending on which division page they are on, the appropriate FAQ's would display for use to have easy access to.
Contain a plugin design for – Contact Us easy form – short form –
Name
Company
Number
Email
Project Details/Questions: Text box

3.)Content Page design
This page should have main area for content
Area for an image with slideshow of other supporting images
Optional area for video – most (99%) of the pages will not have videos, but in the case we do, would like an area that will display videos effectively.
Optional FAQ plugin display
Contact plugin display

Global Elements:

Static and very visible site features that are in a position so that if user clicks beyond home page will still see these are:
Get a Quote
Place Order
Digital Plan-room
Call Today - 555-384-7290

Other global components:
SM Icons – QN, Chirpa, Workrung
Rotating Testimonial

Navigational Menu:
The QVZ Difference
About
Sustainability
Products & Services
Reprograhics
Digital File Management
Color Graphics
Equipment & Supplies
Login
Blog
Contact Us

After the contest – What would be great to have is when a user clicks on one of the departments, it takes that visual element and continues onto it's department page for a smaller but related image - But this may be an after this web design contest.

Additionally will need some other design work on the interior pages, as well, so hoping to find a great designer to complete the other tasks – as well as be the go-to for future endeavors!

Thanks for looking at the project, and I look forward to any questions you may have.
Updates

Looking forward to hearing from interested designers! - If you're curious about my work, you can find my profile at:  https://www.jobrilly.example/users/~07f3b92e61cd5a0b48

Target Market(s)

Please see description

Industry/Entity Type

Electronic

Requirements
Must have
• Please see description

```html
<!DOCTYPE html>
<html lang="en">
<head>
<meta charset="utf-8">
<title>QVZ Digital Imaging</title>
<link href="https://fonts.googleapis.com/css2?family=Montserrat:wght@400;600;700&family=Roboto:wght@300;400&family=Open+Sans:wght@400;600&display=swap" rel="stylesheet">
<style>
:root{
  --navy:#22288a;
  --olive:#5c6b10;
  --olive-text:#6b7a12;
  --ink:#333;
  --muted:#9a9a9a;
  --line:#e2e2e2;
  --topbar:#f2f2f2;
  --dark:#3f3f3f;
  --black:#0b0b0b;
  --cta:#1c9be0;
}
*{box-sizing:border-box;margin:0;padding:0}
html,body{width:1110px;height:1200px;overflow:hidden;background:#fff}
body{position:relative;font-family:"Roboto",sans-serif;color:var(--ink)}
.abs{position:absolute}
.topbar{left:0;top:0;width:1110px;height:25px;background:var(--topbar)}
.toplinks{left:620px;top:6px;font:600 11px "Open Sans",sans-serif;color:#555;display:flex;gap:7px}
.toplinks span.sep{color:#888}
.search{left:857px;top:0;width:142px;height:25px;background:#ddd;font:11px "Open Sans",sans-serif;color:#666;padding:6px 5px}
.search svg{position:absolute;right:6px;top:5px}
.logo{left:111px;top:46px;display:flex;align-items:center;gap:10px}
.logo .mark{width:40px;height:40px;background:var(--navy)}
.logo .name{font:700 26px "Montserrat",sans-serif;color:var(--navy);line-height:1}
.logo .sub{font:700 9px "Montserrat",sans-serif;color:var(--navy);letter-spacing:.5px;margin-top:4px}
.contact{right:111px;top:43px;display:flex;gap:12px;font:300 13px "Roboto",sans-serif;color:#333;align-items:center}
.contact .item{display:flex;align-items:center;gap:5px}
.social{right:111px;top:68px;display:flex;gap:4px}
.social i{display:block;width:22px;height:22px;border-radius:50%}
.nav{left:0;top:113px;width:1110px;height:40px;background:linear-gradient(#2a2a2a,#050505)}
.nav ul{list-style:none;display:flex;position:absolute;left:111px;top:0;height:40px}
.nav li{font:400 13px "Roboto",sans-serif;color:#fff;padding:0 7px;line-height:40px;white-space:nowrap}
.nav li.active{background:var(--navy);padding:0 12px}
.hero{left:0;top:153px;width:1110px;height:291px;background:linear-gradient(100deg,#e9e9ec 0%,#f4f4f6 35%,#dcdde2 60%,#c9b8a8 80%,#e6a23c 92%,#e8e8ea 100%)}
.hero h1{position:absolute;left:111px;top:58px;font:600 28px/32px "Montserrat",sans-serif;color:var(--navy);text-transform:uppercase}
.hero p{position:absolute;left:112px;top:124px;width:345px;font:11.5px/15px "Open Sans",sans-serif;color:#444}
.btn-order{position:absolute;left:114px;top:193px;width:105px;height:31px;background:var(--cta);color:#fff;font:400 13px/31px "Roboto",sans-serif;text-align:center;border:1px solid #137bb5}
.services{left:0;top:444px;width:1110px;height:165px;background:rgba(250,250,250,.95);border-top:1px solid var(--line);border-bottom:1px solid var(--line)}
.svc{position:absolute;top:0;height:165px;text-align:center;padding-top:20px}
.svc + .svc{border-left:1px solid var(--line)}
.svc h3{font:400 15px "Roboto",sans-serif;color:var(--olive-text);margin-top:8px}
.svc p{font:300 11.5px/20px "Roboto",sans-serif;color:var(--muted);margin-top:5px}
.svc.active{background:var(--olive)}
.svc.active h3,.svc.active p{color:#fff}
.svc.active:after{content:"";position:absolute;left:50%;bottom:-10px;margin-left:-11px;border:11px solid transparent;border-bottom:0;border-top:10px solid var(--olive)}
.banner{left:111px;top:637px;width:888px;height:59px;background:var(--dark);border-radius:3px}
.banner p{position:absolute;left:14px;top:12px;width:700px;font:400 13.5px/19px "Montserrat",sans-serif;color:#fff}
.banner .plan{position:absolute;right:15px;top:14px;width:156px;height:32px;background:linear-gradient(#fff,#dedede);border:1px solid #bbb;font:600 13px/30px "Montserrat",sans-serif;color:#333;text-align:center;white-space:nowrap}
h2.title{position:absolute;font:400 16px "Montserrat",sans-serif;color:#333}
.welcome p{position:absolute;left:112px;width:625px;font:300 11px/18.5px "Roboto",sans-serif;color:var(--muted)}
.btn-olive{position:absolute;background:var(--olive);color:#fff;font:400 11px "Roboto",sans-serif;text-align:center}
.field{position:absolute;left:774px;width:225px;border:1px solid var(--line);box-shadow:inset 0 1px 2px #eee;font:italic 300 10px "Roboto",sans-serif;color:#888;padding:7px 10px}
.news{position:absolute;left:113px}
.date{position:absolute;left:0;top:0;width:53px;height:55px;border:1px solid #ccc;text-align:center;font:600 12px/20px "Open Sans",sans-serif;color:#333;padding-top:7px}
.date span{display:block;color:#888;font-size:12px}
.news h4{position:absolute;left:69px;top:0;font:400 15px "Montserrat",sans-serif;color:#222;white-space:nowrap}
.news p{position:absolute;left:69px;top:27px;width:410px;font:300 11px/18.5px "Roboto",sans-serif;color:#555}
.testi{left:624px;top:959px;width:372px;height:171px;border:1px solid #ddd;box-shadow:0 1px 3px #ddd}
.testi .photo{position:absolute;left:19px;top:19px;width:67px;height:70px;border:1px solid #ddd;padding:4px;background:#fff}
.testi .photo div{width:100%;height:100%;background:linear-gradient(#e7c8ae,#c79a7f)}
.testi .dots{position:absolute;right:15px;top:11px;display:flex;gap:3px}
.testi .dots i{width:5px;height:5px;border-radius:50%;background:#bbb}
.testi .dots i:first-child{background:#2a7ad9}
.testi h4{position:absolute;left:110px;top:22px;font:400 16px "Montserrat",sans-serif;color:#222}
.testi .url{position:absolute;left:109px;top:48px;font:italic 300 11px "Roboto",sans-serif;color:var(--olive-text)}
.testi .quote{position:absolute;left:19px;top:77px;width:340px;font:italic 300 12px/18px "Roboto",sans-serif;color:#444}
.testi .quote b{font-weight:300;color:var(--olive-text)}
.testi .who{position:absolute;right:21px;top:144px;font:600 12px "Open Sans",sans-serif;color:#555;display:flex;gap:6px;align-items:center}
.footer{left:0;top:1160px;width:1110px;height:40px;background:var(--black);color:#fff;font:400 11px "Open Sans",sans-serif}
.footer .copy{position:absolute;left:113px;top:13px}
.footer .links{position:absolute;right:111px;top:13px}
</style>
</head>
<body>

<div class="abs topbar"></div>
<div class="abs toplinks"><span>About Us</span><span class="sep">|</span><span>Blog</span><span class="sep">|</span><span>Contact Us</span><span class="sep">|</span><span>Login</span></div>
<div class="abs search">Search...
  <svg width="14" height="14" viewBox="0 0 14 14"><circle cx="5.5" cy="5.5" r="4.2" fill="none" stroke="#555" stroke-width="1.8"/><line x1="8.5" y1="8.5" x2="13" y2="13" stroke="#555" stroke-width="2.2"/></svg>
</div>

<div class="abs logo">
  <div class="mark"></div>
  <div><div class="name">QVZ</div><div class="sub">QUILLVANE PRINT COMPANY, INC.</div></div>
</div>

<div class="abs contact">
  <div class="item"><svg width="14" height="10" viewBox="0 0 14 10"><rect width="14" height="10" fill="var(--navy)"/><path d="M0 0l7 6 7-6" fill="none" stroke="#fff" stroke-width="1"/></svg>hello@qvzprint.example</div>
  <div class="item"><svg width="8" height="14" viewBox="0 0 8 14"><rect x="1" y="0" width="6" height="14" rx="2" fill="var(--navy)"/></svg>+555-384-7290</div>
  <div class="item"><svg width="10" height="14" viewBox="0 0 10 14"><path d="M5 14C5 14 0 7 0 5a5 5 0 0110 0c0 2-5 9-5 9z" fill="var(--navy)"/><circle cx="5" cy="5" r="2" fill="#fff"/></svg>123 First St. Lorem ipsum</div>
</div>
<div class="abs social"><i style="background:#e94e8c"></i><i style="background:#cb2027"></i><i style="background:#3b5fb0"></i><i style="background:#2aa9e0"></i><i style="background:#1d7fc2"></i></div>

<nav class="abs nav"><ul>
  <li class="active">Home</li><li>The QVZ Difference</li><li>Sustainability</li><li>Products &amp; Services</li><li>Reprographics</li><li>Digital File Management</li><li>Color Graphics</li><li>Equipment &amp; Supplies</li>
</ul></nav>

<section class="abs hero" role="img" aria-label="Rolled architectural blueprints beside an open colour swatch fan">
  <h1>Color Service for<br>Designers &amp; Marketers</h1>
  <p>Sed ut perspiciatis unde omnis iste natus error sit voluptatem accus-antium doloremque laudantium, totam rem aperiam, eaque ipsa quae ab illo inventore veritatis et quasi architecto beatae vitae dicta sunt explicabo.</p>
  <div class="btn-order">PLACE ORDER</div>
</section>

<section class="abs services">
  <div class="svc active" style="left:110px;width:219px">
    <svg width="66" height="66" viewBox="0 0 66 66"><g fill="#fff"><rect x="29" y="-4" width="10" height="60" rx="3" transform="rotate(45 33 33)"/><rect x="29" y="8" width="9" height="52" rx="2" transform="rotate(-45 33 33)"/></g></svg>
    <h3>Graphics Imaging Services</h3>
    <p>Lorem ipsum dolor sit amet, consec<br>tetueradipiscing elit, sed diam</p>
  </div>
  <div class="svc" style="left:330px;width:225px">
    <svg width="66" height="66" viewBox="0 0 66 66"><rect x="2" y="8" width="62" height="42" rx="4" fill="none" stroke="var(--olive)" stroke-width="5"/><rect x="22" y="20" width="22" height="18" fill="var(--olive)"/><rect x="20" y="54" width="26" height="5" fill="var(--olive)"/></svg>
    <h3>Reprographics Company</h3>
    <p>Lorem ipsum dolor sit amet, consec<br>tetueradipiscing elit, sed diam</p>
  </div>
  <div class="svc" style="left:556px;width:225px">
    <svg width="66" height="66" viewBox="0 0 66 66"><g fill="none" stroke="var(--olive)" stroke-width="7" stroke-dasharray="5 4"><circle cx="18" cy="26" r="11"/><circle cx="46" cy="16" r="9"/><circle cx="42" cy="48" r="11"/></g></svg>
    <h3>Latest Digital Technology</h3>
    <p>Lorem ipsum dolor sit amet, consec<br>tetueradipiscing elit, sed diam</p>
  </div>
  <div class="svc" style="left:782px;width:225px">
    <svg width="66" height="66" viewBox="0 0 66 66"><g fill="none" stroke="var(--olive)" stroke-width="4"><path d="M4 10h16v42l-8 10-8-10z"/><path d="M25 6h16v46l-8 10-8-10z"/><path d="M46 10h16v42l-8 10-8-10z"/></g></svg>
    <h3>Reprographics</h3>
    <p>Lorem ipsum dolor sit amet, consec<br>tetueradipiscing elit, sed diam</p>
  </div>
</section>

<div class="abs banner">
  <p>Anteposuerit litterarum formas humanitatis per seacula quarta decima et quinta decima. Eodem modo typi, qui nunc nobis videntur parum clari, fiant sollemnes in futurum</p>
  <div class="plan">DIGITAL PLAN-TOOM</div>
</div>

<section class="welcome">
  <h2 class="title" style="left:111px;top:726px">Welcome To&nbsp; QVZ Digital Imaging</h2>
  <p style="top:759px">Sed ut perspiciatis unde omnis iste natus error sit voluptatem accusantium doloremque laudantium, totam rem aperiam, eaqu ipsa quae ab illo inventore veritatis et quasi architecto beatae vitae dicta sunt explicabo. Nemo enim ipsam voluptatem quia voluptas sit aspernatur aut odit aut fugit, sed quia consequuntur magni dolores eos qui ratione voluptatem sequi nesciunt.</p>
  <p style="top:827px">Sed ut perspiciatis unde omnis iste natus error sit voluptatem accusantium doloremque laudantium, totam rem aperiam, eaqu ipsa quae ab illo inventore veritatis et quasi architecto beatae vitae dicta sunt explicabo.</p>
  <div class="btn-olive" style="left:112px;top:876px;width:78px;height:26px;line-height:26px">READ MORE</div>
</section>

<section class="quote">
  <h2 class="title" style="left:777px;top:726px">Get A Quote</h2>
  <div class="field" style="top:759px;height:25px">Enter your name...</div>
  <div class="field" style="top:793px;height:26px">Enter your email...</div>
  <div class="field" style="top:828px;height:58px">Enter your comment...</div>
  <div class="btn-olive" style="left:935px;top:896px;width:64px;height:24px;line-height:24px">SUBMIT</div>
</section>

<h2 class="title" style="left:111px;top:928px">Recnt News</h2>
<div class="news" style="top:958px">
  <div class="date">01<span>Nov</span></div>
  <h4>Lorem ipsum Dolor</h4>
  <p>Sed ut perspiciatis unde omnis iste natus error sit voluptatem accusantium dolore mque laudantium, totam rem aperiam, eaquipsa quae ab illo inventore veritatis</p>
</div>
<div class="news" style="top:1049px">
  <div class="date">01<span>Nov</span></div>
  <h4>Lorem ipsum Dolor</h4>
  <p>Sed ut perspiciatis unde omnis iste natus error sit voluptatem accusantium dolore mque laudantium, totam rem aperiam, eaquipsa quae ab illo inventore veritatis</p>
</div>

<h2 class="title" style="left:629px;top:928px">Testimonials</h2>
<div class="abs testi">
  <div class="dots"><i></i><i></i><i></i><i></i></div>
  <div class="photo"><div role="img" aria-label="Portrait photo of the client giving the testimonial"></div></div>
  <h4>Lorem ipsum Dolor</h4>
  <div class="url">http://www.qvzprint.example</div>
  <p class="quote"><span style="padding-left:91px"></span>Sed ut perspiciatist unde omnis iste natus error<br><span style="padding-left:91px"></span>sit voluptatem accusantium doloremque laud antium, totam rem aperiam, eaqu ipsa quae... <b>read more</b></p>
  <div class="who"><svg width="10" height="11" viewBox="0 0 10 11"><circle cx="5" cy="3" r="3" fill="#888"/><path d="M0 11a5 5 0 0110 0z" fill="#888"/></svg>Jane Doe</div>
</div>

<footer class="abs footer">
  <div class="copy">Copyright © 2013 QVZ Digital Imaging. All Rights Reserved</div>
  <div class="links">Privacy Policy &nbsp;|&nbsp; Terms of use</div>
</footer>

</body>
</html>
```